Christmas Collection Candle Label Design

Looking to update our existing Christmas Candle Collection labels. Labels should reflect the overall feel of our brand- www.kelvanoro.ca
Want to include some color elements. Holiday colors added into design but more muted/ earthy tones not vibrant colors . Metallic elements and line art botanical illustration. Fonts should be more align to brand
Scents
Holiday Tree
Candy Cane
Sugar and Spice
Joyeaux Noel

```html
<!DOCTYPE html>
<html lang="en">
<head>
<meta charset="utf-8">
<title>Amber &amp; Clove – Candle Label</title>
<link href="https://fonts.googleapis.com/css2?family=Cormorant+Garamond:wght@500&family=Marcellus&family=Tenor+Sans&family=Allura&display=swap" rel="stylesheet">
<style>
  :root {
    --backdrop: #b3c9cf;
    --label-teal: #0f2a36;
    --label-teal-deep: #0b222c;
    --leaf-green: #2f7a45;
    --leaf-dark: #173f33;
    --band-light: #3f8a57;
    --band-dark: #27603a;
    --blush: #eadcd7;
    --rule: #c9bfbd;
  }
  * { margin: 0; padding: 0; box-sizing: border-box; }
  html, body {
    width: 771px; height: 1200px; overflow: hidden;
    background: var(--backdrop);
  }
  .label {
    position: absolute;
    left: 36px; top: 250px;
    width: 700px; height: 700px;
    background: var(--label-teal);
    box-shadow: 2px 3px 6px rgba(0,0,0,0.25);
    overflow: hidden;
    color: var(--blush);
    text-align: center;
  }
  .foliage-side {
    position: absolute; top: 0; bottom: 65px; width: 150px;
  }
  .foliage-side.left { left: 0; background: linear-gradient(90deg, var(--label-teal-deep), rgba(15,42,54,0)); }
  .foliage-side.right { right: 0; background: linear-gradient(270deg, var(--label-teal-deep), rgba(15,42,54,0)); }
  .foliage-top {
    position: absolute; left: 0; top: 0; width: 700px; height: 170px;
    background: linear-gradient(180deg, var(--leaf-green) 0%, #246a3e 45%, var(--leaf-dark) 80%, rgba(15,42,54,0) 100%);
  }
  .foliage-bottom {
    position: absolute; left: 0; top: 545px; width: 700px; height: 90px;
    background: linear-gradient(0deg, var(--leaf-green) 0%, #225f3a 50%, rgba(15,42,54,0) 100%);
  }
  .tagline {
    position: absolute; left: 0; right: 0; top: 180px;
    font-family: "Marcellus", serif;
    font-size: 17px; line-height: 22px; letter-spacing: 2px;
  }
  .tagline-rule {
    position: absolute; left: 322px; top: 236px;
    width: 56px; height: 2px; background: var(--blush);
  }
  .scent-name {
    position: absolute; left: 0; right: 0; top: 245px;
    font-family: "Cormorant Garamond", serif;
    font-weight: 500;
    font-size: 86px; line-height: 86px; letter-spacing: 3px;
  }
  .scent-script {
    position: absolute; left: 0; right: 0; top: 338px;
    font-family: "Allura", cursive;
    font-size: 130px; line-height: 150px;
    padding-left: 10px;
  }
  .notes {
    position: absolute; left: 142px; top: 507px;
    width: 390px; height: 30px;
    border-top: 1px solid var(--rule);
    border-bottom: 1px solid var(--rule);
    font-family: "Marcellus", serif;
    font-size: 14px; line-height: 28px; letter-spacing: 3px;
  }
  .info-band {
    position: absolute; left: 0; bottom: 0; width: 700px; height: 65px;
    background: linear-gradient(90deg, var(--band-light), var(--band-dark));
    display: flex; align-items: center; justify-content: center;
    font-family: "Tenor Sans", sans-serif;
    font-size: 17px; letter-spacing: 2px;
  }
  .info-band span { padding: 0 22px; }
  .info-band span + span { border-left: 2px solid var(--blush); }
</style>
</head>
<body>
  <main class="label">
    <div class="foliage-side left" role="img" aria-label="Dark palm frond silhouettes along the left edge"></div>
    <div class="foliage-side right" role="img" aria-label="Dark palm frond silhouettes along the right edge"></div>
    <div class="foliage-top" role="img" aria-label="Green tropical palm and monstera leaves across the top"></div>
    <div class="foliage-bottom" role="img" aria-label="Green tropical palm and monstera leaves along the bottom"></div>

    <p class="tagline">MADE WITH<br>PLANT BASED BOTANICAL</p>
    <div class="tagline-rule"></div>
    <h1 class="scent-name">AMBER &amp;</h1>
    <p class="scent-script">Clove</p>
    <p class="notes">TUBEROSE - GARDENIA - PATACHOLI</p>

    <footer class="info-band">
      <span>Net WT.10oz/283g</span>
      <span>Made in Canada</span>
      <span>Verdell Soy</span>
    </footer>
  </main>
</body>
</html>
```